zAvora Corporate Website

zAvora is a well-funded start up developing an Online Marketing Platform for small businesses in Europe.
We are launching in February 2012 with all-in-one online marketing services including professional website, DIY SEO, Dashboard with Reports and Online marketing tools, and Support.
Our internal web designer has come up with a preliminary website design which we wish to continue to improve using new ideas, colours, layout, image, etc.
The brief is very simple - improve the website whether it is look & feel, ease of use, conversion rate - we are looking for overall improvements.
The contest will last 5 days and we will award the winner £300.
If you are the winner , you will also be required to provide designs for 3 more internal pages adhering to the proposed home page design.
Judging criteria : -
Visual Design
Layout must adhere to best practices and wire frame. If you decide to move elements around significantly please provide reason
Functional, informative and drives calls to action
Industry/Entity Type
Marketing
Look and feel
Each slider illustrates characteristics of the customer's brand and the style your logo design should communicate.

```html
<!DOCTYPE html>
<html lang="en">
<head>
<meta charset="utf-8">
<title>zAvora – Online Marketing for Small Business Websites</title>
<link href="https://fonts.googleapis.com/css2?family=Arimo:wght@400;700&family=Oswald:wght@400;500;700&family=Varela+Round&display=swap" rel="stylesheet">
<style>
:root{
  --page:#e9f1f8;
  --page-hi:#f5f9fc;
  --ink:#2a2a2a;
  --body:#3a3a3a;
  --muted:#666;
  --brand:#1a8fe0;
  --brand-dark:#0b63c8;
  --hero-a:#1f6fe6;
  --hero-b:#3aa2f5;
  --orange:#ff9a12;
  --orange-dark:#f06d00;
  --band:#a9d1f5;
  --box-line:#9fc9ea;
  --footer:#262626;
  --footer-line:#3a3a3a;
  --footer-text:#c9c9c9;
  --red:#d81f1f;
  --amber:#f29a12;
  --green:#3b9d1c;
  --tab:#7a7a7a;
}
*{box-sizing:border-box;margin:0;padding:0}
html,body{width:818px;height:1200px;overflow:hidden}
body{position:relative;background:linear-gradient(#dfeaf4,var(--page-hi) 40%,var(--page));font-family:"Arimo",Arial,sans-serif;color:var(--ink)}
.abs{position:absolute}

/* header */
.top-links{top:11px;left:564px;font-size:7.5px;color:#444;letter-spacing:.2px;word-spacing:1px}
.top-links span{margin:0 6px;color:#777}
.brand{top:30px;left:108px;display:flex;align-items:center;gap:6px;font-family:"Varela Round",sans-serif;font-size:38px;color:#1d1d1d}
.brand-dot{width:44px;height:44px;border-radius:50%;background:var(--brand)}
.tabs{top:69px;left:566px;display:flex;gap:3px}
.tab{height:29px;background:linear-gradient(#9a9a9a,var(--tab));color:#fff;font-size:9px;display:flex;align-items:center;justify-content:center;border-radius:2px 2px 0 0}
.tab.home{width:26px;background:#f1f1f1;border:1px solid #ddd}
.tab.tour{width:55px}.tab.price{width:54px}

/* hero */
.hero{top:99px;left:103px;width:611px;height:234px;border-radius:6px;overflow:hidden;background:linear-gradient(110deg,var(--hero-a),var(--hero-b) 70%,#5cbaf8);box-shadow:0 6px 10px rgba(0,40,90,.18)}
.hero h1{position:absolute;left:57px;top:17px;font-family:"Varela Round",sans-serif;font-size:21px;line-height:24px;color:#fff;font-weight:400;text-shadow:0 1px 2px rgba(0,0,60,.4)}
.hero ul{position:absolute;left:57px;top:78px;list-style:none}
.hero li{font-family:"Varela Round",sans-serif;color:#fff;font-size:14px;height:23px;display:flex;align-items:center;gap:14px}
.hero li svg{width:18px;height:12px}
.cta{position:absolute;left:153px;top:182px;width:107px;height:37px;border-radius:4px;background:linear-gradient(var(--orange),var(--orange-dark));border:1px solid #ffc46b;color:#fff;text-align:center}
.cta small{display:block;font-size:8px;margin-top:4px}
.cta b{display:block;font-family:"Varela Round",sans-serif;font-size:17px;font-weight:400}
.tag{position:absolute;height:14px;padding:0 8px;background:#eef6fd;border:1px solid #c7dff3;font-size:6.5px;color:#333;display:flex;align-items:center;justify-content:center;box-shadow:0 1px 2px rgba(0,0,0,.2)}
.portrait{position:absolute;left:478px;top:114px;width:133px;height:120px;border-radius:50% 40% 0 0;background:linear-gradient(#d9a585,#3b6bb8 70%)}

/* tagline */
.tagline{top:369px;left:0;width:818px;text-align:center;font-size:20px;color:#2b2b2b;font-weight:400;letter-spacing:-.3px}
.tagline em{font-style:normal;color:var(--brand)}
.quote{top:392px;left:0;width:818px;text-align:center;font-size:15px;color:#444;letter-spacing:-.3px}

/* offers */
.offers{top:432px;left:102px;width:613px;height:110px;background:var(--band);border-radius:6px;box-shadow:0 4px 8px rgba(0,40,90,.15)}
.offer{position:absolute;top:8px;width:142px;height:94px;border-radius:3px;overflow:hidden;color:#fff;font-family:"Oswald",sans-serif}
.offer.setup{left:6px;background:linear-gradient(#e23a2a,var(--red))}
.offer.pro{left:158px;background:linear-gradient(#fdb52a,var(--amber) 50%,#d9471a)}
.offer.turbo{left:307px;background:linear-gradient(#5bb52b,var(--green))}
.offer .t1{position:absolute;left:10px;top:6px;font-size:19px;font-weight:700;color:#ffe23a;line-height:20px}
.offer .t2{position:absolute;left:10px;top:27px;font-size:24px;font-weight:700;line-height:26px}
.offer.turbo .t1{color:#fff;font-size:17px}
.offer.turbo .t2{top:24px;font-size:17px}
.offer .t3{position:absolute;left:12px;top:58px;font-size:8px;color:#ffe23a;font-weight:500}
.offer.turbo .t3{top:46px}
.offer .foot{position:absolute;left:0;right:0;bottom:0;height:20px;background:rgba(0,0,0,.35);font-size:10px;display:flex;align-items:center;justify-content:center;font-weight:400}
.offer.setup .foot{font-size:13px;height:24px}
.offer.turbo .foot{height:30px;font-size:9.5px;line-height:12px;text-align:center;background:rgba(0,40,0,.35)}
.offer .ribbon{position:absolute;right:-22px;top:14px;width:90px;height:16px;background:#1d6fd6;transform:rotate(50deg);font-size:9px;text-align:center;line-height:16px;font-weight:500}
.offer.pro .ribbon,.offer.turbo .ribbon{background:#e0301c}
.offer .art{position:absolute;right:14px;top:38px;width:36px;height:30px;border-radius:4px;background:rgba(255,255,255,.3)}
.how{position:absolute;left:468px;top:12px;width:140px}
.how h3{font-family:"Oswald",sans-serif;font-size:12px;color:#fff;font-weight:500;text-shadow:0 1px 1px rgba(0,50,100,.4)}
.how p{margin-top:8px;font-size:7.5px;line-height:11.5px;color:#26445e}

/* about */
.about-title{top:567px;left:110px;font-size:20px;color:var(--brand);font-weight:400}
.about{top:596px;left:109px;width:599px;font-size:7.4px;line-height:11.6px;color:var(--body)}
.about p{margin-bottom:11.6px}
.about span{color:var(--brand)}

/* features */
.feature{position:absolute;top:737px;width:141px;height:63px;background:#f4f9fd;border:1px solid var(--box-line);border-radius:3px}
.feature svg{position:absolute;left:7px;top:14px;width:28px;height:28px}
.feature h4{position:absolute;left:38px;top:9px;font-size:13px;color:var(--brand);font-weight:400}
.feature p{position:absolute;left:38px;top:29px;right:6px;font-size:7.2px;line-height:9.5px;color:#555}

/* examples */
.ex-title{top:855px;left:128px;font-size:11.5px;line-height:12px;color:var(--brand);font-weight:700}
.ex-text{top:889px;left:128px;width:138px;font-size:7.5px;line-height:11.5px;color:#444}
.ex-more{top:958px;left:212px;font-size:7.5px;color:var(--brand);display:flex;align-items:center;gap:4px}
.ex-more i{width:8px;height:8px;border:1px solid #aaa;border-radius:50%;display:inline-block}
.shot{position:absolute;background:linear-gradient(#f6f6f6,#dfe3e7)}
.shot.back1{left:320px;top:832px;width:70px;height:130px}
.shot.back2{left:600px;top:832px;width:66px;height:130px;background:linear-gradient(#2a2a2a,#1a4f9a 60%,#222)}
.shot.front{left:369px;top:827px;width:237px;height:141px;border:3px solid var(--green);background:linear-gradient(#262626 0 20px,#f4f4f4 20px 72%,#e6e6e6)}
.shot.front span{position:absolute;left:20px;top:4px;color:#fff;font-size:9px;font-weight:700;font-style:italic}

/* footer */
.footer{top:1000px;left:0;width:818px;height:200px;background:var(--footer);border-top:4px solid #6fb3e6}
.foot-brand{top:990px;left:103px;width:114px;height:61px;background:linear-gradient(#2f9ff0,#1479c9);display:flex;align-items:center;justify-content:center;gap:5px;font-family:"Varela Round",sans-serif;font-size:19px;color:#fff}
.foot-brand i{width:26px;height:26px;border-radius:50%;background:#fff;opacity:.9}
.fcol{position:absolute;top:1024px}
.fcol h5{display:flex;align-items:center;gap:8px;font-size:12.5px;color:#fff;font-weight:400;height:28px;border-bottom:1px solid var(--footer-line)}
.fcol h5 svg{width:22px;height:22px}
.fcol ul{list-style:none;margin-top:4px}
.fcol li{font-size:7.4px;color:var(--footer-text);height:19px;line-height:19px;border-bottom:1px solid var(--footer-line);padding-left:9px;position:relative}
.fcol li:before{content:"";position:absolute;left:1px;top:8px;border-left:3px solid var(--brand);border-top:2px solid transparent;border-bottom:2px solid transparent}
.follow{top:1066px;left:112px;font-size:12px;color:#ddd}
.soc{position:absolute;top:1085px;width:22px;height:22px;border-radius:50%;background:#f2f2f2;border:2px solid #bbb}
.email{top:1066px;left:608px;width:84px;height:15px;background:#fff;border-radius:2px;font-size:6.5px;color:#aaa;padding:4px 5px;font-style:italic}
.plus{top:1066px;left:693px;width:18px;height:15px;background:#3aaa2a;color:#fff;font-weight:700;font-size:13px;line-height:14px;text-align:center}
.like{top:1107px;left:608px;display:flex;gap:3px;font-size:6.5px}
.like b{background:#e9ecf3;border:1px solid #8ea0c4;color:#334;padding:1px 4px;font-weight:400;display:flex;align-items:center;gap:3px}
.like b i{width:6px;height:6px;background:#3b5a9a;display:inline-block}
.like span{background:#fff;border:1px solid #999;color:#333;padding:1px 3px}
.copy{top:1164px;left:0;width:818px;text-align:center;font-size:7.5px;color:#bbb;letter-spacing:.2px}
.copy a{color:var(--brand);text-decoration:none}
</style>
</head>
<body>

<header>
  <nav class="abs top-links">ABOUT US<span>|</span>CONTACT US<span>|</span>LOGIN</nav>
  <div class="abs brand"><i class="brand-dot"></i>zAvora</div>
  <nav class="abs tabs">
    <div class="tab home"><svg width="16" height="14" viewBox="0 0 16 14"><path d="M8 1 1 7h2v6h4V9h2v4h4V7h2z" fill="#666"/></svg></div>
    <div class="tab tour">Quick Tour</div>
    <div class="tab price">Pricing</div>
  </nav>
</header>

<section class="abs hero">
  <svg class="abs" style="left:0;top:0" width="230" height="234"><g fill="#fff" opacity=".08"><circle cx="40" cy="190" r="60"/><circle cx="20" cy="60" r="30"/><circle cx="110" cy="40" r="22"/><circle cx="150" cy="220" r="30"/></g></svg>
  <h1>Getting a website has never<br>been so simple</h1>
  <ul>
    <li><svg viewBox="0 0 18 12"><path d="M0 4h10V0l8 6-8 6V8H0z" fill="#fff"/></svg>Business Websites</li>
    <li><svg viewBox="0 0 18 12"><path d="M0 4h10V0l8 6-8 6V8H0z" fill="#fff"/></svg>Online Marketing</li>
    <li><svg viewBox="0 0 18 12"><path d="M0 4h10V0l8 6-8 6V8H0z" fill="#fff"/></svg>Dashboard Controls</li>
    <li><svg viewBox="0 0 18 12"><path d="M0 4h10V0l8 6-8 6V8H0z" fill="#fff"/></svg>Full Setup &amp; Support</li>
  </ul>
  <div class="cta"><small>Sign up NOW for</small><b>FREE!</b></div>

  <div class="tag" style="left:314px;top:93px;width:55px">PPC</div>
  <div class="tag" style="left:346px;top:113px;width:56px">Email Marketing</div>
  <div class="tag" style="left:406px;top:84px;width:55px">Testimonials</div>
  <div class="tag" style="left:403px;top:102px;width:55px">Deals</div>
  <div class="tag" style="left:465px;top:86px;width:55px">Hosting</div>
  <div class="tag" style="left:461px;top:113px;width:55px">Images</div>
  <div class="tag" style="left:392px;top:124px;width:56px">Search Ads</div>
  <div class="tag" style="left:326px;top:137px;width:57px">Directories</div>
  <div class="tag" style="left:371px;top:150px;width:57px">Blogs /News</div>
  <div class="tag" style="left:423px;top:139px;width:57px">SEO</div>
  <div class="tag" style="left:434px;top:165px;width:57px">Referrals</div>
  <div class="tag" style="left:353px;top:172px;width:57px">Social Pages</div>
  <div class="tag" style="left:393px;top:187px;width:57px">Micro Feeds</div>
  <div class="tag" style="left:491px;top:102px;width:57px">Website Design</div>
  <div class="tag" style="left:539px;top:91px;width:70px">Content Management</div>
  <div class="tag" style="left:545px;top:106px;width:57px">Reporting</div>
  <div class="portrait" role="img" aria-label="Photo of a puzzled businessman scratching his head"></div>
</section>

<h2 class="abs tagline">The Complete Online Marketing Solution for <em>Small Business Websites</em></h2>
<p class="abs quote">“Get a big online presence and more sales leads in 30 minutes”</p>

<section class="abs offers">
  <div class="offer setup">
    <div class="t1">Free</div><div class="t2">SETUP</div>
    <div class="art" role="img" aria-label="Illustration of an open box with a download arrow"></div>
    <div class="ribbon">£199 Value</div>
    <div class="foot">WEB OFFER ONLY</div>
  </div>
  <div class="offer pro">
    <div class="t1">Pro</div><div class="t2">PACKAGE</div>
    <div class="t3">Big online presence</div>
    <div class="art" role="img" aria-label="Illustration of a cardboard package"></div>
    <div class="ribbon">£22 /month</div>
    <div class="foot">Bussiness Website &amp; Easy Dashboard</div>
  </div>
  <div class="offer turbo">
    <div class="t1">TURBO SALES</div><div class="t2">PRO PLUS</div>
    <div class="t3">More sales LEADS</div>
    <div class="art" role="img" aria-label="Illustration of a box with a headset character"></div>
    <div class="ribbon">£29 /month</div>
    <div class="foot">Bussiness Website,<br>Easy Dashboard &amp; ppc Sales</div>
  </div>
  <div class="how">
    <h3>How does it work?</h3>
    <p>Neque porro quisquam est qui dolorem ipsum quia dolor vel eum iriure dolor in hendrerit in vulputate velit dou site vesse molestie consequat, vel illumsit amet, adipisci velit"</p>
  </div>
</section>

<h2 class="abs about-title">About Us</h2>
<section class="abs about">
  <p><span>zAvora</span> will build your business website, optimise SEO marketing and make recommendations on best practices to help you win customers. Let our team of experts design a business website for you. Choose a business website from <span>zAvora's</span> broad array of fabulous, customisable business websites and our experts will have your business online in minutes. <span>zAvora</span> lets you create a professional business website without the need to know how to code or programme.</p>
  <p>Your business website comes with automatic Internet marketing, marketing on the Internet is easy with <span>zAvora</span>, we automatically optimise your site for SEO marketing and we can run search ad campaigns when you need them. Get a business website with online marketing now. <span>zAvora</span> brings your Small Business Website to LIFE!</p>
  <p>View our example business websites above, watch the video demo to see how to make a business website or call us now and get your business marketing online today. The <span>zAvora</span> website builder gives you a professional online appearance - post your own images, give customers your latest news and create customer testimonials, it's the most complete online marketing solution for your business.</p>
</section>

<div class="feature" style="left:109px">
  <svg viewBox="0 0 28 28"><rect x="2" y="10" width="5" height="16" fill="#2a8fe0"/><rect x="9" y="4" width="5" height="22" fill="#2a8fe0"/><rect x="16" y="16" width="5" height="10" fill="#6bb8f0"/><rect x="22" y="19" width="5" height="7" fill="#6bb8f0"/></svg>
  <h4>Case Studies</h4><p>Read real stories about small businesses online</p>
</div>
<div class="feature" style="left:262px">
  <svg viewBox="0 0 28 28"><circle cx="14" cy="11" r="8" fill="none" stroke="#2a8fe0" stroke-width="2"/><rect x="11" y="19" width="6" height="6" fill="#2a8fe0"/></svg>
  <h4>How to</h4><p>Learn from our online marketing tips for small business</p>
</div>
<div class="feature" style="left:415px">
  <svg viewBox="0 0 28 28"><path d="M2 4h16v11H8l-4 4v-4H2z" fill="#2a8fe0"/><path d="M10 10h16v11h-3v4l-4-4h-9z" fill="#6bb8f0"/></svg>
  <h4>News &amp; Chatter</h4><p>Get up-to-date news and chatter about online marketing</p>
</div>
<div class="feature" style="left:568px">
  <svg viewBox="0 0 28 28"><circle cx="14" cy="15" r="11" fill="#2a8fe0"/><circle cx="14" cy="15" r="8" fill="#e8f4fd"/><path d="M14 9v6h4" stroke="#2a8fe0" stroke-width="2" fill="none"/><rect x="12" y="1" width="4" height="3" fill="#2a8fe0"/></svg>
  <h4>Demo</h4><p>Find out what zAvora can do for your business.</p>
</div>

<h3 class="abs ex-title">View examples of our<br>stunning business websites</h3>
<p class="abs ex-text">Duis autem vel eum iriure dolor in hendrerit in vulputate velit esse molestie consequat, vel illum dolore eu feugiat nulla facilisis at vero eros et accumsan. esse molestie.</p>
<div class="abs ex-more"><i></i>View more</div>
<svg class="abs" style="left:291px;top:884px" width="14" height="28"><path d="M14 0v28L0 14z" fill="#9aa4ae"/></svg>
<svg class="abs" style="left:685px;top:884px" width="14" height="28"><path d="M0 0v28L14 14z" fill="#7cc3f0"/></svg>
<div class="shot back1" role="img" aria-label="Screenshot of a light example business website"></div>
<div class="shot back2" role="img" aria-label="Screenshot of a dark example business website"></div>
<div class="shot front" role="img" aria-label="Screenshot of a featured example business website"><span>Sample Site</span></div>

<footer>
  <div class="abs footer"></div>
  <div class="abs foot-brand"><i></i>zAvora</div>
  <div class="abs follow">Follow</div>
  <div class="soc" style="left:112px"></div>
  <div class="soc" style="left:143px"></div>
  <div class="soc" style="left:175px"></div>

  <div class="fcol" style="left:225px;width:135px">
    <h5><svg viewBox="0 0 22 22"><circle cx="11" cy="11" r="7" fill="none" stroke="#777" stroke-width="4" stroke-dasharray="3 2"/><circle cx="11" cy="11" r="3" fill="#777"/></svg>OurServices</h5>
    <ul><li>Search Engine Optimization (SEO)</li><li>Social Media</li><li>Web Analytics</li></ul>
  </div>
  <div class="fcol" style="left:376px;width:97px">
    <h5><svg viewBox="0 0 22 22"><rect x="4" y="1" width="14" height="20" rx="2" fill="#777"/><rect x="6" y="4" width="10" height="13" fill="#333"/></svg>ContactUs</h5>
    <ul><li>Contact Us</li><li>Customer Support</li><li>Request a call back</li><li>FAQ's</li></ul>
  </div>
  <div class="fcol" style="left:490px;width:104px">
    <h5><svg viewBox="0 0 22 22"><path d="M1 4h7l2 2h10v13H1z" fill="#777"/></svg>Navigation</h5>
    <ul><li>Site Map</li><li>Terms and Condition</li><li>Privacy &amp; Policy</li><li>Get in Touch</li></ul>
  </div>
  <div class="fcol" style="left:608px;width:103px">
    <h5><svg viewBox="0 0 22 22"><rect x="1" y="4" width="20" height="14" fill="#777"/><path d="M1 4l10 8 10-8" stroke="#333" fill="none"/></svg>Subscribe</h5>
  </div>
  <div class="abs email">Type your email here</div>
  <div class="abs plus">+</div>
  <div class="abs like"><b><i></i>Like</b><span>62</span></div>

  <p class="abs copy">Copyright © 2011 zAvora Pvt. Ltd 2011 -&nbsp; All rights reserved.&nbsp; Managed by <a>zAvora</a> &nbsp;&nbsp;|&nbsp;&nbsp; Admin</p>
</footer>

</body>
</html>
```